Media Services Start-up -- Corporate Website and Logo Design. Inspiration required!

We need a logo design and corporate website design, including coding, for our start-up business.
Vennatra’s value proposition is based on bringing together media content from a vast number of geographies globally, adding human and AI curation, translation and editing, and delivering the content using tailored customer interfaces. On the one hand, the business brings together media coverage from all over the world, and on the other it brings together content, human skills and technology to deliver a supreme customer experience.
Vennatra is a B2B media monitoring and analytics business with emphasis on global customers. Vennatra's service offering is centred around sourcing media content from different markets, processing, storing and delivering the content and insights derived from it using an online platform / mobile app.
The messaging we want to create through the logo is:
- Global scope
- Speed of delivery
- Cost-efficiency
- Multi-lingual
- Tailor-made
- Trustworthy
Target Market(s)
Business to business, PR / Communications, Media, Marketing
Logo Text
Vennatra
Coding
Coded - Design and coding required
Number of Pages Required
5+ page
Font styles to use
Other font styles liked:
- See Design Brief for details
Colors
Designer to choose colors to be used in the design.

```html
<!DOCTYPE html>
<html lang="en">
<head>
<meta charset="utf-8">
<title>Vennatra — Global Media Intelligence</title>
<link href="https://fonts.googleapis.com/css2?family=Roboto:wght@500;700&family=Outfit:wght@300;400;500&display=swap" rel="stylesheet">
<style>
  :root {
    --teal: #3bb09f;
    --ink: #1c1c1c;
    --nav-ink: #333333;
    --white: #ffffff;
    --field-line: #c9c9c9;
    --field-text: #555555;
    --hero-dark: #2e3336;
    --hero-mid: #4d5459;
    --hero-light: #7b8a90;
  }
  * { box-sizing: border-box; margin: 0; padding: 0; }
  html, body { width: 1200px; height: 635px; overflow: hidden; }
  body { position: relative; background: var(--white); font-family: "Outfit", sans-serif; color: var(--ink); }

  .site-header { position: absolute; top: 0; left: 0; width: 1200px; height: 92px; background: var(--white); }
  .brand { position: absolute; left: 141px; top: 22px; font-family: "Roboto", sans-serif; font-weight: 700; font-size: 34px; letter-spacing: -0.3px; color: var(--ink); }
  .main-nav { position: absolute; top: 36px; left: 0; font-size: 14.5px; color: var(--nav-ink); font-weight: 400; }
  .main-nav a { position: absolute; white-space: nowrap; color: inherit; text-decoration: none; }
  .main-nav a.is-active { color: #000; font-weight: 500; }
  .btn-signin { position: absolute; left: 967px; top: 30px; width: 92px; height: 33px; background: var(--teal); color: var(--white); font-size: 14px; font-weight: 500; display: flex; align-items: center; justify-content: center; }

  .hero { position: absolute; top: 92px; left: 0; width: 1200px; height: 493px; overflow: hidden; }
  .hero-photo { position: absolute; inset: 0; background:
      radial-gradient(ellipse 420px 260px at 620px 260px, rgba(20,22,24,0.55), transparent 70%),
      linear-gradient(100deg, var(--hero-light) 0%, var(--hero-mid) 35%, var(--hero-dark) 65%, #565d60 100%); }
  .hero-title { position: absolute; left: 139px; top: 160px; font-family: "Roboto", sans-serif; font-weight: 700; font-size: 46px; line-height: 51px; color: var(--white); text-transform: uppercase; letter-spacing: -0.3px; }
  .hero-lead { position: absolute; left: 143px; top: 274px; width: 462px; font-size: 15px; line-height: 23.5px; color: var(--white); font-weight: 400; }
  .hero-lead strong { font-weight: 500; }

  .lead-card { position: absolute; left: 755px; top: 108px; width: 304px; height: 292px; background: var(--white); }
  .lead-card h2 { position: absolute; top: 32px; left: 0; width: 100%; text-align: center; font-family: "Roboto", sans-serif; font-weight: 500; font-size: 19.5px; color: var(--ink); }
  .field { position: absolute; left: 28px; width: 248px; height: 35px; border: 1px solid var(--field-line); display: flex; align-items: center; padding-left: 10px; font-size: 11px; color: var(--field-text); }
  .field svg { margin-right: 8px; }
  .btn-start { position: absolute; left: 28px; top: 221px; width: 248px; height: 35px; background: var(--teal); color: var(--white); font-size: 15.5px; font-weight: 500; display: flex; align-items: center; justify-content: center; }

  .site-footer { position: absolute; top: 585px; left: 0; width: 1200px; height: 50px; background: var(--teal); }
  .copyright { position: absolute; left: 141px; top: 17px; font-size: 12px; color: var(--white); }
  .social { position: absolute; top: 11px; width: 28px; height: 28px; border: 1.3px solid var(--white); border-radius: 50%; display: flex; align-items: center; justify-content: center; }
</style>
</head>
<body>
  <header class="site-header">
    <div class="brand">Vennatra</div>
    <nav class="main-nav">
      <a class="is-active" style="left:427px">Home</a>
      <a style="left:501px">Solutions</a>
      <a style="left:596px">How We Do It</a>
      <a style="left:721px">Our People</a>
      <a style="left:830px">Our Technology</a>
    </nav>
    <div class="btn-signin">SIGN IN</div>
  </header>

  <section class="hero">
    <div class="hero-photo" role="img" aria-label="Blurred photo of a person holding a tablet showing charts at a desk"></div>
    <h1 class="hero-title">Delivering Global<br>Media Intelligence</h1>
    <p class="hero-lead"><strong>Vennatra</strong> is an international media intelligence service provider. We help communications teams builds and operate truly global media monitoring and measurement programmes.</p>
    <form class="lead-card">
      <h2>Learn More about Vennatra</h2>
      <div class="field" style="top:73px">
        <svg width="14" height="14" viewBox="0 0 14 14" fill="none" stroke="#777" stroke-width="1"><circle cx="7" cy="4.5" r="3"/><path d="M1.5 13.5 C1.5 9 12.5 9 12.5 13.5 Z"/></svg>Name*
      </div>
      <div class="field" style="top:123px">
        <svg width="15" height="12" viewBox="0 0 15 12" fill="none" stroke="#777" stroke-width="1"><rect x="0.5" y="0.5" width="14" height="11" rx="1.5"/><path d="M1 1.5 L7.5 7 L14 1.5"/></svg>Email*
      </div>
      <div class="field" style="top:172px">
        <svg width="14" height="14" viewBox="0 0 14 14" fill="none" stroke="#777" stroke-width="1"><path d="M3 1 L5.5 3.5 L4 5.5 C5 8 6 9 8.5 10 L10.5 8.5 L13 11 L11 13 C6 13 1 8 1 3 Z"/></svg>Phone*
      </div>
      <div class="btn-start">GET STARTED</div>
    </form>
  </section>

  <footer class="site-footer">
    <p class="copyright">© 2019 Vennatra Analytics Media. All rights reserved.</p>
    <span class="social" style="left:925px" aria-label="Share">
      <svg width="14" height="14" viewBox="0 0 14 14" fill="none" stroke="#fff" stroke-width="1.4"><circle cx="3" cy="7" r="1.8"/><circle cx="11" cy="3" r="1.8"/><circle cx="11" cy="11" r="1.8"/><path d="M4.6 6.2 L9.4 3.8 M4.6 7.8 L9.4 10.2"/></svg>
    </span>
    <span class="social" style="left:960px" aria-label="Message">
      <svg width="14" height="14" viewBox="0 0 14 14" fill="none" stroke="#fff" stroke-width="1.4" stroke-linejoin="round"><path d="M1.5 2.5 H12.5 V9.5 H6 L3 12 V9.5 H1.5 Z"/></svg>
    </span>
    <span class="social" style="left:996px" aria-label="Email">
      <svg width="14" height="12" viewBox="0 0 14 12" fill="none" stroke="#fff" stroke-width="1.4"><rect x="1" y="1.5" width="12" height="9" rx="1"/><path d="M1.5 2 L7 6.5 L12.5 2"/></svg>
    </span>
    <span class="social" style="left:1031px" aria-label="Link">
      <svg width="14" height="14" viewBox="0 0 14 14" fill="none" stroke="#fff" stroke-width="1.4" stroke-linecap="round"><path d="M6 8 L8 6"/><path d="M5 6.5 L3.2 8.3 A2 2 0 0 0 5.7 10.8 L7.5 9"/><path d="M9 7.5 L10.8 5.7 A2 2 0 0 0 8.3 3.2 L6.5 5"/></svg>
    </span>
  </footer>
</body>
</html>
```